Specialised investor in e-mobility and energy wants business card design

We need a business card design that fits our existing corporate design. <The look and feel must be 'sharp'/'clean', dynamic, communicate momentum, professionalism etc (as one would imagine from a firm in the financial sector). We like the idea of a reverse-side of the card that includes the logo, and the name and contact details on the other. We expect the deliverable to be whatever format might be required to be able to get cards printed directly by a service such as kelmo press. Our website is www.zub.capital

```html
<!DOCTYPE html>
<html lang="en">
<head>
<meta charset="utf-8">
<title>Zub Capital – Business Card</title>
<link href="https://fonts.googleapis.com/css2?family=Montserrat:wght@300;400;700&display=swap" rel="stylesheet">
<style>
  :root{
    --page:#3a3c40;
    --ink:#ffffff;
    --ink-soft:#e8eee0;
    --night-blue:#17304a;
    --teal:#1f5a5e;
    --olive:#5f6a22;
    --olive-deep:#3f4a1c;
    --brand-green:#4a6b2a;
  }
  *{box-sizing:border-box;margin:0;padding:0}
  html,body{width:1200px;height:887px;overflow:hidden}
  body{background:var(--page);font-family:'Montserrat',sans-serif;color:var(--ink);position:relative}
  .card{position:absolute;width:620px;height:400px;border-radius:28px;overflow:hidden}
  .card--front{left:60px;top:40px}
  .card--back{left:520px;top:450px}
  .card__photo{position:absolute;inset:0;
    background:linear-gradient(125deg,var(--night-blue) 0%,var(--teal) 38%,var(--olive) 72%,var(--olive-deep) 100%)}
  .wordmark{position:absolute;font-weight:300;letter-spacing:1px;white-space:nowrap;line-height:1}
  .card--front .wordmark{left:150px;top:160px;font-size:72px;color:var(--ink)}
  .card--back .wordmark{right:40px;top:40px;font-size:44px;color:var(--ink)}
  .contact{position:absolute;left:36px;top:70px;font-size:13px;font-weight:300;line-height:1.3}
  .contact__name{font-weight:700;font-size:18px;letter-spacing:.5px}
  .contact__role{font-size:14px;margin-bottom:8px}
  .contact__line{display:flex;align-items:center;gap:10px;font-size:15px;margin-left:20px}
  .contact__line svg{width:14px;height:14px;flex:none}
  .team{margin-top:12px}
  .team__member{margin-left:60px;margin-top:8px;font-size:15px}
  .team__member .contact__line{margin-left:10px}
  .office{position:absolute;right:40px;bottom:130px;text-align:right;font-size:16px;font-weight:300;line-height:1.4;color:var(--ink-soft)}
</style>
</head>
<body>
  <section class="card card--front">
    <div class="card__photo" role="img" aria-label="Night city street with skyscrapers and light trails"></div>
    <div class="wordmark">zub capital</div>
  </section>

  <section class="card card--back">
    <div class="card__photo" role="img" aria-label="Night city street with skyscrapers and light trails"></div>
    <div class="wordmark">zub capital</div>

    <div class="contact">
      <div class="contact__name">PETER ALLWOOD</div>
      <div class="contact__role">team directly</div>
      <div class="contact__line">
        <svg viewBox="0 0 16 16"><path fill="#fff" d="M3 2h3l1 3-2 1a8 8 0 0 0 5 5l1-2 3 1v3c0 1-1 1-2 1A12 12 0 0 1 2 4c0-1 0-2 1-2z"/></svg>
        +41 79555 0148</div>
      <div class="contact__line">
        <svg viewBox="0 0 16 16"><rect x="1" y="3" width="14" height="10" fill="#fff"/><path d="M1 3l7 6 7-6" fill="none" stroke="#5f6a22" stroke-width="1.4"/></svg>
        peter@zub.capital</div>
      <div class="contact__line">
        <svg viewBox="0 0 16 16"><circle cx="8" cy="8" r="7" fill="#fff"/><path d="M1 8h14M8 1c-3 3-3 11 0 14M8 1c3 3 3 11 0 14" fill="none" stroke="#5f6a22" stroke-width="1"/></svg>
        www.zub.capital</div>

      <div class="team">
        <div class="team__member">Kenji Arata
          <div class="contact__line"><svg viewBox="0 0 16 16"><rect x="1" y="3" width="14" height="10" fill="#fff"/><path d="M1 3l7 6 7-6" fill="none" stroke="#5f6a22" stroke-width="1.4"/></svg>kenji@zub.capital</div>
        </div>
        <div class="team__member">Daniel Moreau
          <div class="contact__line"><svg viewBox="0 0 16 16"><rect x="1" y="3" width="14" height="10" fill="#fff"/><path d="M1 3l7 6 7-6" fill="none" stroke="#5f6a22" stroke-width="1.4"/></svg>daniel@zub.capital</div>
        </div>
        <div class="team__member">Clara Fenwick
          <div class="contact__line"><svg viewBox="0 0 16 16"><rect x="1" y="3" width="14" height="10" fill="#fff"/><path d="M1 3l7 6 7-6" fill="none" stroke="#5f6a22" stroke-width="1.4"/></svg>clara@zub.capital</div>
        </div>
      </div>
    </div>

    <div class="office">Zub Capital S.A<br>Geneva, Switzerland</div>
  </section>
</body>
</html>
```